Accounting firm needing business card / letterhead designed
Marcus L. Trenholm, CPA
marcus@veltrowledger.com
www.veltrowledger.com
842 E Alder Ave Harlow Bend, ME 43827
419-562-0974

```html
<!DOCTYPE html>
<html lang="en">
<head>
<meta charset="utf-8">
<title>Veltrow Ledger – Business Card</title>
<link rel="stylesheet" href="https://fonts.googleapis.com/css2?family=Roboto:wght@400;500&family=Roboto+Condensed:wght@700&display=swap">
<style>
  :root {
    --backdrop: #bdbdbd;
    --paper: #f7f7f7;
    --navy: #25215f;
    --lime: #8cc63f;
    --white: #ffffff;
    --grey-text: #555555;
  }
  * { margin: 0; padding: 0; box-sizing: border-box; }
  html, body { width: 1200px; height: 960px; overflow: hidden; }
  body {
    position: relative;
    background: var(--backdrop);
    font-family: "Roboto", Arial, sans-serif;
  }
  .card {
    position: absolute;
    overflow: hidden;
  }
  .card--front {
    left: 320px; top: 100px; width: 606px; height: 345px;
    border-radius: 18px;
    background: var(--paper);
  }
  .card--back {
    left: 320px; top: 493px; width: 600px; height: 343px;
    border-radius: 16px;
    background: var(--lime);
  }
  .wordmark {
    position: absolute;
    font-weight: 500;
    color: var(--navy);
    letter-spacing: 2px;
    white-space: nowrap;
  }
  .card--front .wordmark {
    left: 0; width: 100%; top: 138px;
    text-align: center;
    font-size: 40px;
  }
  .front-url {
    position: absolute;
    left: 0; width: 100%; top: 290px;
    text-align: center;
    font-size: 13px;
    letter-spacing: 6.5px;
    color: var(--grey-text);
  }
  .card--back .wordmark {
    left: 34px; top: 70px;
    font-size: 25px;
    letter-spacing: 1.5px;
  }
  .name-band {
    position: absolute;
    left: 308px; top: 38px; width: 292px; height: 56px;
    background: var(--navy);
    clip-path: polygon(6% 0, 100% 0, 100% 100%, 0 100%);
    display: flex; align-items: center;
    padding-left: 44px;
  }
  .name-band__name {
    font-family: "Roboto Condensed", "Arial Narrow", sans-serif;
    font-weight: 700;
    font-size: 21px;
    color: var(--white);
    white-space: nowrap;
  }
  .address {
    position: absolute;
    left: 35px; top: 209px;
    font-size: 14px;
    line-height: 19px;
    color: var(--white);
    font-style: normal;
  }
  .contacts {
    position: absolute;
    left: 36px; top: 256px;
    list-style: none;
    font-size: 14px;
    line-height: 19px;
    color: var(--white);
  }
  .contacts__item { display: flex; align-items: center; gap: 8px; }
  .contacts__icon { width: 14px; height: 14px; fill: var(--navy); flex: none; }
</style>
</head>
<body>
  <section class="card card--front">
    <div class="wordmark">VELTROW LEDGER</div>
    <div class="front-url">www.veltrowledger.com</div>
  </section>

  <section class="card card--back">
    <div class="wordmark">VELTROW LEDGER</div>
    <div class="name-band"><span class="name-band__name">Marcus L. Trenholm, CPA</span></div>
    <address class="address">842 E Alder Ave<br>Harlow Bend, ME 43827</address>
    <ul class="contacts">
      <li class="contacts__item">
        <svg class="contacts__icon" viewBox="0 0 24 24"><path d="M6.6 10.8a15.1 15.1 0 0 0 6.6 6.6l2.2-2.2c.3-.3.7-.4 1-.2 1.1.4 2.3.6 3.6.6.6 0 1 .4 1 1V20c0 .6-.4 1-1 1A17 17 0 0 1 3 4c0-.6.4-1 1-1h3.5c.6 0 1 .4 1 1 0 1.3.2 2.5.6 3.6.1.3 0 .7-.2 1z"/></svg>
        419-562-0974
      </li>
      <li class="contacts__item">
        <svg class="contacts__icon" viewBox="0 0 24 24"><path d="M2 5h20v14H2z M4 7v.5l8 5 8-5V7l-8 5z" fill-rule="evenodd"/></svg>
        marcus@veltrowledger.com
      </li>
      <li class="contacts__item">
        <svg class="contacts__icon" viewBox="0 0 24 24"><circle cx="12" cy="12" r="10"/><path d="M2 12h20M12 2c3 3 3 17 0 20M12 2c-3 3-3 17 0 20" stroke="#8cc63f" stroke-width="1.6" fill="none"/></svg>
        www.veltrowledger.com
      </li>
    </ul>
  </section>
</body>
</html>
```